I need a business card designed using the logo provided either vertical or horizontal......Harbourline Property Group is an Australian based real estate company that caters for the upper end of the market so the design of the business card "must reflect" the companies image!!
Colour combinations are optional but "must be realistic" and must be able to be accurately useable CMYK colours.
Please consider that any colours used "must be able to be used" and be suitable in following designs for "pull out banner signs" and "real estate signs".
The colours and the font in the attached designs are for example and other combinations are encouraged.
Target Market(s)
The High End of the Australian real estate market
Industry/Entity Type
Business
Contact Information for Business Card
Logo - Business Name - Director + Licensed Real Estate Agent - Mobile Number (Cell Phone) - Business Number - Fax - Email Address - Web address
Requirements
Must have
- Designs and colours (CMYK) that can easily be interpreted by an Australian printer.
Nice to have
- Some alternative ideas on colour and font..........the ones provided are ok and have been provided as an example but I am looking for alternative ideas
Should not have
- Loud, overly bright colours. Designs that do not reflect the professional standards of the business.
- Designs that look good on a computer monitor but can not be re-created on a printing press.............this is most important when it comes to shading etc.

```html
<!DOCTYPE html>
<html lang="en">
<head>
<meta charset="utf-8">
<title>Harbourline Property Group – Business Card</title>
<link href="https://fonts.googleapis.com/css2?family=Lato:wght@400&display=swap" rel="stylesheet">
<style>
  :root {
    --backdrop: #161616;
    --card: #2c2d30;
    --gold-light: #d9c28e;
    --gold: #c1862f;
    --silver: #c9c9c9;
    --text-light: #d2d2d2;
  }
  html, body {
    margin: 0;
    padding: 0;
    overflow: hidden;
  }
  body {
    width: 1200px;
    height: 900px;
    background: var(--backdrop);
    position: relative;
    font-family: "Lato", Arial, sans-serif;
  }
  .card {
    position: absolute;
    background: var(--card);
    border-radius: 16px;
  }
  .card--front {
    left: 322px;
    top: 112px;
    width: 570px;
    height: 331px;
  }
  .card--back {
    left: 327px;
    top: 486px;
    width: 559px;
    height: 324px;
  }
  .brand {
    position: absolute;
    text-align: center;
    text-transform: uppercase;
    font-weight: 400;
    line-height: 1.25;
  }
  .brand__square {
    display: block;
    width: 34px;
    height: 34px;
    margin: 0 auto 16px;
  }
  .card--front .brand {
    left: 40px;
    width: 226px;
    top: 112px;
    color: var(--gold-light);
    font-size: 19px;
    letter-spacing: 2px;
  }
  .card--front .brand__square {
    background: var(--gold);
  }
  .card--back .brand {
    left: 0;
    width: 559px;
    top: 92px;
    color: var(--silver);
    font-size: 24px;
    letter-spacing: 3px;
  }
  .card--back .brand__square {
    background: var(--silver);
    width: 40px;
    height: 40px;
  }
  .contact {
    position: absolute;
    left: 298px;
    top: 118px;
    color: var(--text-light);
  }
  .contact__name {
    margin: 0;
    font-size: 27px;
    font-weight: 400;
    line-height: 1;
  }
  .contact__first { color: var(--gold-light); }
  .contact__last { color: var(--gold); }
  .contact__role {
    margin: 4px 0 0 1px;
    font-size: 16px;
  }
  .contact__details {
    margin: 22px 0 0 4px;
    font-size: 16px;
    line-height: 1.3;
    font-style: normal;
  }
</style>
</head>
<body>
  <section class="card card--front">
    <div class="brand">
      <span class="brand__square"></span>
      Harbourline<br>Property Group
    </div>
    <div class="contact">
      <h1 class="contact__name"><span class="contact__first">Daniel</span> <span class="contact__last">Hartley</span></h1>
      <p class="contact__role">Managing Director</p>
      <address class="contact__details">
        info@harbourlinegroup.com<br>
        044-987 654 321
      </address>
    </div>
  </section>

  <section class="card card--back">
    <div class="brand">
      <span class="brand__square"></span>
      Harbourline<br>Property Group
    </div>
  </section>
</body>
</html>
```